Graphics Design of Physics Book

Hi
Size : 8" x 11.25"
We are education book Publication Company and would like to have book cover for "Physics" it has 4 volumes. All 4 having the same color scheme and design except the volume no.
Blue is my personal favorite but u can use any color. Want to have a band at the bottom of the cover to place our Logo “VORNA Education” a PDF of the same is attached, or you can place logo anywhere according to ur design.
I need “Physics” as title of the book to be visible prominently.
And volume and volume no. should also be Visible and eye catching I prefer a Graphic to enhance the Volume No.
A background pattern can also be a option (it should be vector form so that color can be change later)
Please do not offer any cut and paste design I need very professional presentation.
Volume and Number can be in metallic 3D (CMYK) effect.
only Professional presentation will get feedback.
I have provided a sample artwork for reference do not follow it but can be a reference what I needed !

Target Market(s)

Students Class 9th to 12th

Industry/Entity Type

Education

Font styles to use
Serif

Colors
3176b5
0555a3
85abd2
cadf82
abd036
9bcb3c

Requirements
Must have
• Eye catching.
• “Physics” as title of the book to be visible prominently.
• volume and volume no. should also be Visible and eye catching
• I prefer a Graphic to enhance the Volume No.
• Icons for
• 1. Questions and answers
• 2. Theory Notes
• 3. Tips & Tricks
• 4. Previous Year's Reference Questions
• 5. Covers Complete Syllabus
Nice to have
• decent seamless background or metallic 3d effect (not to be print in special Ink) design should only be in CMYK.
Should not have
• Physics related Pictures or Icons (Specially E=mc2) or any scientist photograph or I Need pure graphic design

```html
<!DOCTYPE html>
<html lang="en">
<head>
<meta charset="utf-8">
<title>Physics 2 – Book Cover</title>
<link rel="stylesheet" href="https://fonts.googleapis.com/css2?family=Fredoka:wght@600;700&family=Roboto+Condensed:wght@400;700&display=swap">
<style>
  :root {
    --blue-title: #2a78b8;
    --blue-deep: #0555a3;
    --blue-mid: #3176b5;
    --blue-soft: #85abd2;
    --icon-ink: #3a2f7a;
    --label-ink: #2b2b4a;
    --gold: #e2a52a;
    --logo-ink: #1a1a1a;
    --paper: #ffffff;
  }
  * { margin: 0; padding: 0; box-sizing: border-box; }
  html, body { width: 849px; height: 1200px; overflow: hidden; background: var(--paper); }
  .cover {
    position: relative;
    width: 849px;
    height: 1200px;
    overflow: hidden;
    background: var(--paper);
  }
  .light-burst {
    position: absolute;
    top: 200px;
    left: 0;
    width: 849px;
    height: 760px;
    background:
      radial-gradient(ellipse 40% 30% at 32% 45%, rgba(255,255,255,0.95) 0%, rgba(255,255,255,0) 70%),
      linear-gradient(180deg, rgba(255,255,255,0) 0%, rgba(133,171,210,0.55) 18%, rgba(49,118,181,0.55) 50%, rgba(133,171,210,0.45) 78%, rgba(255,255,255,0) 100%);
  }
  .title {
    position: absolute;
    top: 108px;
    left: 0;
    width: 100%;
    text-align: center;
    font-family: "Fredoka", sans-serif;
    font-weight: 700;
    font-size: 152px;
    letter-spacing: 6px;
    color: var(--blue-title);
    line-height: 1;
  }
  .volume-number {
    position: absolute;
    top: 440px;
    left: 470px;
    width: 320px;
    font-family: "Fredoka", sans-serif;
    font-weight: 700;
    font-size: 560px;
    line-height: 1;
    text-align: center;
    color: var(--gold);
  }
  .features {
    position: absolute;
    top: 950px;
    left: 40px;
    width: 769px;
    display: flex;
    justify-content: space-between;
  }
  .feature {
    width: 140px;
    display: flex;
    flex-direction: column;
    align-items: center;
    text-align: center;
  }
  .feature-icon { width: 56px; height: 56px; }
  .feature-icon.round { border-radius: 50%; background: var(--icon-ink); }
  .feature-icon.square { border-radius: 8px; background: var(--icon-ink); }
  .feature-icon.square.deep { background: var(--blue-deep); }
  .feature-icon.outline { border-radius: 6px; border: 4px solid var(--blue-mid); width: 44px; }
  .feature-label {
    margin-top: 14px;
    font-family: "Roboto Condensed", sans-serif;
    font-size: 17px;
    line-height: 1.2;
    color: var(--label-ink);
  }
  .brand {
    position: absolute;
    top: 1108px;
    left: 0;
    width: 100%;
    display: flex;
    justify-content: center;
    align-items: center;
    gap: 12px;
  }
  .brand-mark { width: 18px; height: 18px; background: var(--logo-ink); }
  .brand-name {
    font-family: "Roboto Condensed", sans-serif;
    font-weight: 700;
    font-size: 34px;
    letter-spacing: 2px;
    color: var(--logo-ink);
  }
</style>
</head>
<body>
<main class="cover">
  <div class="light-burst" role="img" aria-label="Abstract burst of translucent blue light bars rising from the lower left"></div>

  <h1 class="title">PHYSICS</h1>

  <p class="volume-number" aria-label="Volume 2">2</p>

  <section class="features">
    <div class="feature">
      <div class="feature-icon round" role="img" aria-label="Questions and answers icon"></div>
      <p class="feature-label">Questions<br>&amp; Answers</p>
    </div>
    <div class="feature">
      <div class="feature-icon round" role="img" aria-label="Tips and tricks icon"></div>
      <p class="feature-label">Tips &amp; Tricks</p>
    </div>
    <div class="feature">
      <div class="feature-icon square deep" role="img" aria-label="Theory notes icon"></div>
      <p class="feature-label">Theory Notes</p>
    </div>
    <div class="feature">
      <div class="feature-icon square" role="img" aria-label="Previous year's questions icon"></div>
      <p class="feature-label">Previous Year's<br>Reference Questions</p>
    </div>
    <div class="feature">
      <div class="feature-icon outline" role="img" aria-label="Complete syllabus icon"></div>
      <p class="feature-label">Covers Complete<br>Syllabus</p>
    </div>
  </section>

  <footer class="brand">
    <span class="brand-mark"></span>
    <span class="brand-name">VORNA Education</span>
  </footer>
</main>
</body>
</html>
```